E-mailer for Invitation to a Webinar - based on cricket theme

We are an e-learning development organization. We are conducting a webinar and want to send this flyer as a e-Mail Newsletter where we would like people to click on the Register button and reach our registration page & register for the webinar.
I am looking for an e-mailer to be sent to prospective customers to participate in a Webinar. The e-Mailer must be based on Cricket theme. It will have the following sections:
- One short paragraph 2-3 sentences about the webinar.
- One Heading and 5 bullet points about the webinar.
- Another subheading and 5 bullet points about the benefits of attending the webinar.
- 1 Paragraph (4-5 sentences) describing the profile of the presenter.
- Place to display the date, time and Link to register for the Webinar.
- Place to display a list of the designation of business executives who must attend the webinar (Who Can Attend)
- Place to announce a Sweepstake (Tablo Petit for one lucky registrant)
The target group is Senior Management HR Professionals in Australia & Newzealand.
Here is the text to be used in the webinar:
Webinar Title: mLearning Boundary Webinar
Sub Title: Smash out googlies of mLearning and be a winner
Para 1: Converting your existing eLearning programs to mLearning has its own set of unpredictable challenges. Taking you on the batting front, Q-Prism plans to showcase how to smash out the 20 googlies of this match.
Sub Heading 1: Common mLearning Googlies
Bulletpoints:
- Do I need to start from scratch?
- Is unification possible? Mobile with Web?
- Will it make it a hole in my pocket?
- Which is the right development tool for me?
- Can mLearning be equally effective?
Sub Heading 2: Key Takeaways-
- Transit to mLearning cost-effectively
- Strategies for unifying web and mobile learning
- Pros & Cons of various development tools
- Samples of effective mLearning modules
- Hottest trends of mLearning
The pitch is ready! Join us for this exciting match on May 10 @ 2 PM ADT. Register for the Webinar Now!
Webinar Presenter
Hi All, I am Ritika Mehra, an eLearning enthusiast and I
believe in drafting innovating solutions to increase uptake
of virtual learning. ANZ has been our key geography since
2011 and the response has been awesome! Off lately, I
can see that most of the organizations are facing
challenges around re-purposing existing e-Courses for tab/mobile delivery, and I plan to present solutions to them in this session. Please feel free to share your thoughts/questions and I shall plan to address them for you. Connect to me at: e-mail address.
Date: 10 May 2013
Time: 2:00 PM ADT to 3:00 PM ADT
Duration: 1 Hour
Target Market(s)
Senior HR Professionals / Training professionals from Australia & Newzealand
Industry/Entity Type
Business
Requirements
Must have
- It must have strong call to action (Register Button) somewhere at Top/Mid/Bottom part of the flyer.
Please use a cricket player's silhouette/ Ilustration/ vector preferable on the top.
Please use cricket ground and cricket elements as theme.
Nice to have
- Must gel with the colour themes of our website - http://www.lumorvex-learning.net

```html
<!DOCTYPE html>
<html lang="en">
<head>
<meta charset="utf-8">
<title>mLearning Boundary Webinar – Q-Prism</title>
<link rel="stylesheet" href="https://fonts.googleapis.com/css2?family=Anton&family=Arimo:ital,wght@0,400;0,700;1,700&family=Roboto+Condensed:wght@300;400;700&display=swap">
<style>
  :root {
    --stage: #2a2a2a;
    --paper: #ffffff;
    --mist: #eef0f1;
    --teal: #3fcfd0;
    --teal-deep: #1fb5ba;
    --teal-pale: #bdeef0;
    --orange: #f26a1b;
    --orange-deep: #d9530c;
    --ink: #333333;
    --ink-soft: #555555;
    --grass: #86b84a;
    --link-blue: #3a8fd0;
    --crowd: #d6d6d6;
  }
  * { box-sizing: border-box; margin: 0; padding: 0; }
  html, body { width: 849px; height: 1200px; overflow: hidden; }
  body { background: var(--stage); font-family: "Arimo", Arial, sans-serif; color: var(--ink); position: relative; }

  .mailer { position: absolute; left: 183px; top: 85px; width: 486px; height: 1028px; background: var(--paper); overflow: hidden; }
  .mailer > * { position: absolute; }

  /* Header */
  .hero-art { left: 0; top: 0; width: 486px; height: 300px;
    background: linear-gradient(160deg, #f4f6f7 0%, #dff5f6 30%, var(--teal-pale) 55%, #e9f7f8 80%, #ffffff 100%); }
  .pitch-art { left: 60px; top: 150px; width: 220px; height: 95px; background: linear-gradient(150deg, #a9cf6e, var(--grass)); transform: skewX(-18deg); opacity: .85; }
  .batsman { left: 52px; top: 22px; width: 118px; height: 200px; background: linear-gradient(180deg, #f47a2c, var(--orange-deep)); border-radius: 40px 40px 20px 20px; }
  .brand { right: 20px; top: 20px; font-family: "Roboto Condensed", Arial, sans-serif; font-weight: 700; font-size: 17px; color: #6a6a6a; letter-spacing: .5px; display: flex; align-items: center; gap: 5px; }
  .brand-dot { width: 8px; height: 8px; background: var(--orange); border-radius: 50%; }

  .title { left: 150px; top: 82px; transform: rotate(-4deg); transform-origin: left top; }
  .title-top { font-family: "Anton", Impact, sans-serif; font-size: 30px; color: #3d3d3d; letter-spacing: 1px; line-height: 1; padding-left: 4px; }
  .title-banner { margin-top: 3px; background: var(--orange); color: var(--paper); font-family: "Anton", Impact, sans-serif; font-size: 28px; letter-spacing: 1px; padding: 4px 12px; line-height: 1.1; box-shadow: 2px 3px 0 rgba(0,0,0,.12); }
  .subtitle { left: 158px; top: 168px; transform: rotate(-4deg); transform-origin: left top; background: var(--teal-deep); color: #1f3b3f; font-family: "Arimo", Arial, sans-serif; font-weight: 700; font-size: 11.5px; padding: 5px 10px; }

  /* Teal intro band */
  .intro-band { left: 0; top: 290px; width: 486px; height: 100px; background: linear-gradient(180deg, var(--teal) 0%, #57d6d6 100%); }
  .intro-band-edge { left: 0; top: 382px; width: 486px; height: 22px; }
  .intro-text { left: 30px; top: 310px; width: 300px; font-size: 10.4px; line-height: 1.42; color: #173a3d; text-align: center; }

  .prize-badge { left: 330px; top: 228px; width: 140px; height: 130px; }
  .prize-tablet { position: absolute; left: 30px; top: 0; width: 80px; height: 82px; border-radius: 6px; background: linear-gradient(160deg, #f5f5f5, #b9c3cc); }
  .prize-badge svg { position: absolute; left: 0; top: 40px; }
  .prize-label { position: absolute; left: 0; top: 78px; width: 140px; text-align: center; color: var(--paper); font-weight: 700; font-size: 13px; }
  .prize-cta { position: absolute; left: 0; top: 97px; width: 140px; text-align: center; color: var(--paper); font-weight: 700; font-size: 10px; }

  /* Googlies & takeaways */
  .topics { left: 20px; top: 418px; width: 232px; }
  .topic-head { display: flex; align-items: center; gap: 6px; color: var(--orange); font-weight: 700; font-size: 11px; margin-bottom: 12px; }
  .topic-head svg { flex: none; }
  .topic-list { list-style: none; padding-left: 25px; margin-bottom: 14px; }
  .topic-list li { font-size: 9.2px; line-height: 1.48; color: var(--ink); position: relative; padding-left: 12px; }
  .topic-list li::before { content: ""; position: absolute; left: 0; top: 4px; border-left: 5px solid var(--orange); border-top: 3px solid transparent; border-bottom: 3px solid transparent; }
  .divider { left: 255px; top: 420px; width: 1px; height: 200px; background: #f3b27a; }

  .schedule-bg { left: 262px; top: 400px; width: 224px; height: 230px; background: radial-gradient(ellipse at center, #e6e8ea 0%, #f2f3f4 55%, rgba(255,255,255,0) 80%); }
  .webinar-flag { left: 280px; top: 416px; width: 160px; height: 62px; border-radius: 40px 50px 50px 40px; background: linear-gradient(90deg, #ffc23a, var(--orange) 60%, #c8243a); display: flex; align-items: center; justify-content: center; }
  .webinar-flag span { font-family: "Arimo", Arial, sans-serif; font-style: italic; font-weight: 700; font-size: 22px; color: #3a2a10; background: #f9d34a; padding: 0 10px; transform: rotate(-6deg); }
  .schedule-head { left: 326px; top: 490px; color: var(--orange); font-style: italic; font-weight: 700; font-size: 14px; }
  .schedule { left: 314px; top: 512px; border-collapse: collapse; font-size: 10.4px; font-weight: 700; color: #444; }
  .schedule td { padding: 3px 0; height: 19px; }
  .schedule td.key { width: 42px; }
  .schedule td.sep { width: 24px; color: #aaa; font-weight: 400; text-align: center; }
  .register-btn { left: 312px; top: 596px; width: 106px; height: 22px; border-radius: 11px; background: linear-gradient(180deg, #f05a3a, #c72a14); color: var(--paper); font-style: italic; font-weight: 700; font-size: 12px; display: flex; align-items: center; justify-content: center; box-shadow: 0 2px 3px rgba(0,0,0,.25); text-decoration: none; }

  .pitch-strip { left: 20px; top: 648px; width: 435px; height: 22px; background: var(--teal); color: #1e3235; font-style: italic; font-weight: 700; font-size: 12px; display: flex; align-items: center; justify-content: center; border-radius: 2px; }

  /* Presenter */
  .presenter { left: 20px; top: 690px; width: 310px; height: 140px; border-radius: 0 0 6px 6px; box-shadow: 1px 2px 3px rgba(0,0,0,.18); }
  .presenter-title { position: absolute; left: 8px; top: 2px; background: #262626; color: var(--paper); font-family: "Roboto Condensed", Arial, sans-serif; font-size: 14px; padding: 1px 10px; border-radius: 3px; letter-spacing: .5px; }
  .presenter-photo { position: absolute; left: 12px; top: 32px; width: 60px; height: 55px; background: linear-gradient(180deg, #c9b3a5, #6f5c55); border: 1px solid #ccc; }
  .presenter-bio { position: absolute; left: 12px; top: 30px; width: 290px; font-size: 7.6px; line-height: 1.62; color: var(--ink-soft); }
  .presenter-bio .spacer { float: left; width: 70px; height: 58px; }

  .audience { left: 340px; top: 688px; width: 115px; height: 143px; background: var(--orange); border-radius: 4px; color: var(--paper); padding: 6px 8px; box-shadow: 0 2px 3px rgba(0,0,0,.2); }
  .audience-small { font-family: "Roboto Condensed", Arial, sans-serif; font-size: 10.5px; }
  .audience-big { font-family: "Roboto Condensed", Arial, sans-serif; font-weight: 300; font-size: 25px; line-height: 1; margin-bottom: 8px; }
  .audience ul { list-style: none; }
  .audience li { font-size: 7.8px; line-height: 1.35; margin-bottom: 5px; position: relative; padding-left: 9px; }
  .audience li::before { content: ""; position: absolute; left: 0; top: 2.5px; border-left: 4px solid var(--paper); border-top: 2.5px solid transparent; border-bottom: 2.5px solid transparent; }

  /* Sweepstake */
  .crowd { left: 0; top: 840px; width: 486px; height: 160px; background: linear-gradient(180deg, rgba(255,255,255,0) 0%, #ececec 45%, var(--crowd) 100%); }
  .sweep-head { left: 0; top: 850px; width: 486px; text-align: center; color: var(--orange); font-size: 18px; }
  .sweep-sub { left: 0; top: 873px; width: 486px; text-align: center; font-size: 9.2px; color: #333; }
  .sweep-tablet { left: 204px; top: 898px; width: 66px; height: 100px; border-radius: 6px; background: linear-gradient(170deg, #ffffff, #c7ccd2 60%, #e9b58f); border: 1px solid #cfd3d8; }

  /* Footer */
  .footer { left: 0; top: 1000px; width: 486px; height: 28px; background: #f4f4f4; display: flex; align-items: center; justify-content: space-between; padding: 0 22px 0 20px; }
  .footer-link { display: flex; align-items: center; gap: 5px; color: var(--link-blue); font-weight: 700; font-size: 10px; text-decoration: none; }
  .follow { display: flex; align-items: center; gap: 4px; font-size: 7px; color: #666; background: var(--paper); padding: 2px 4px; }
  .follow span.social { width: 14px; height: 14px; border-radius: 50%; background: var(--link-blue); display: inline-block; }
</style>
</head>
<body>
<main class="mailer">
  <!-- Header -->
  <div class="hero-art" role="img" aria-label="Soft teal watercolour splash backdrop with stadium floodlights"></div>
  <div class="pitch-art" role="img" aria-label="Green cricket pitch patch"></div>
  <div class="batsman" role="img" aria-label="Orange silhouette of a cricket batsman swinging a bat"></div>
  <div class="brand"><span class="brand-dot"></span>Q-Prism</div>

  <h1 class="title">
    <div class="title-top">MLEARNING</div>
    <div class="title-banner">BOUNDARY WEBINAR</div>
  </h1>
  <p class="subtitle">Smash out googlies of mLearning and be a winner</p>

  <!-- Intro band -->
  <div class="intro-band"></div>
  <svg class="intro-band-edge" width="486" height="22" viewBox="0 0 486 22" aria-hidden="true">
    <path d="M0 0H486V8L460 14 430 9 400 16 360 10 330 17 290 11 250 16 210 9 170 15 130 10 90 17 50 11 20 15 0 10Z" fill="#57d6d6"/>
  </svg>
  <p class="intro-text">Converting your existing eLearning programs to mLearning has its own set of unpredictable challenges. Taking you on the batting front, Q-Prism plans to showcase how to smash out the 20 googlies of this match.</p>

  <a class="prize-badge" href="#register" aria-label="Win Tablo Petit – Register Now">
    <div class="prize-tablet" role="img" aria-label="Two Tablo Petit tablets"></div>
    <svg width="140" height="90" viewBox="0 0 140 90" aria-hidden="true">
      <polygon points="70,0 80,14 96,6 98,24 116,22 108,38 124,46 108,54 116,70 98,68 96,86 80,78 70,90 60,78 44,86 42,68 24,70 32,54 16,46 32,38 24,22 42,24 44,6 60,14" fill="#f26a1b"/>
      <path d="M4 32 Q70 20 136 32 L130 58 Q70 46 10 58 Z" fill="#1f5f8b"/>
    </svg>
    <span class="prize-label">Win Tablo Petit</span>
    <span class="prize-cta">Register Now</span>
  </a>

  <!-- Topics -->
  <section class="topics">
    <h2 class="topic-head">
      <svg width="22" height="22" viewBox="0 0 22 22" aria-hidden="true"><polygon points="11,1 13,8 21,9 14,13 17,21 11,16 5,21 8,13 1,9 9,8" fill="none" stroke="#f26a1b" stroke-width="1.6"/></svg>
      Common mLearning Googlies
    </h2>
    <ul class="topic-list">
      <li>Do I need to start from scratch?</li>
      <li>Is unification possible? Mobile with Web?</li>
      <li>Will it make it a hole in my pocket?</li>
      <li>Which is the right development tool for me?</li>
      <li>Can mLearning be equally effective?</li>
    </ul>
    <h2 class="topic-head">
      <svg width="22" height="22" viewBox="0 0 22 22" aria-hidden="true"><polygon points="11,1 13,8 21,9 14,13 17,21 11,16 5,21 8,13 1,9 9,8" fill="none" stroke="#f26a1b" stroke-width="1.6"/></svg>
      Key Takeaways
    </h2>
    <ul class="topic-list">
      <li>Transit to mLearning cost-effectively</li>
      <li>Strategies for unifying web and mobile learning</li>
      <li>Pros &amp; Cons of various development tools</li>
      <li>Samples of effective mLearning modules</li>
      <li>Hottest trends of mLearning</li>
    </ul>
  </section>
  <div class="divider"></div>

  <!-- Schedule -->
  <div class="schedule-bg"></div>
  <div class="webinar-flag" role="img" aria-label="Flaming cricket ball with Webinar label"><span>Webinar</span></div>
  <h3 class="schedule-head">Date &amp; Time</h3>
  <table class="schedule">
    <tr><td class="key">Date</td><td class="sep">|</td><td>10 May 2013</td></tr>
    <tr><td class="key">Day</td><td class="sep">|</td><td>Friday</td></tr>
    <tr><td class="key">Time</td><td class="sep">|</td><td>2:00 PM ADT</td></tr>
    <tr><td class="key">Duration</td><td class="sep">|</td><td>1 Hour</td></tr>
  </table>
  <a class="register-btn" href="#register">Register Now</a>

  <p class="pitch-strip">The pitch is ready! Join us for this exciting match on May 10 @ 2 PM AEST.</p>

  <!-- Presenter -->
  <section class="presenter">
    <h2 class="presenter-title">WEBINAR PRESENTER</h2>
    <div class="presenter-photo" role="img" aria-label="Portrait photo of presenter Ritika Mehra"></div>
    <p class="presenter-bio"><span class="spacer"></span>Hi All, I am Ritika Mehra, an eLearning enthusiast and I believe in drafting innovating solutions to increase uptake of virtual learning. ANZ has been our key geography since 2011 and the response has been awesome! Off lately, I can see that most of the organizations are facing challenges around re-purposing existing e-Courses for tab/mobile delivery, and I plan to present solutions to them in this session. Please feel free to share your thoughts/questions and I shall plan to address them for you. Connect to me at: ritikam@lumorvex-learning.net.</p>
  </section>

  <aside class="audience">
    <div class="audience-small">Who Can</div>
    <div class="audience-big">Attend</div>
    <ul>
      <li>CXOs, VPs, Directors of eLearning &amp; Online Education organizations</li>
      <li>Supervisors, Managers, Directors and VPs of Corporate L&amp;D unit</li>
      <li>Senior learning &amp; design professionals</li>
    </ul>
  </aside>

  <!-- Sweepstake -->
  <div class="crowd" role="img" aria-label="Grey silhouettes of a cheering stadium crowd"></div>
  <h2 class="sweep-head">Register for Webinar &amp; Win a Tablo Petit*</h2>
  <p class="sweep-sub">One lucky webinar attendee will be given an Tablo Petit at the end of the webinar.</p>
  <div class="sweep-tablet" role="img" aria-label="Hand holding a Tablo Petit tablet"></div>

  <!-- Footer -->
  <footer class="footer">
    <a class="footer-link" id="register" href="http://www.lumorvex-learning.net">
      <svg width="11" height="11" viewBox="0 0 11 11" aria-hidden="true"><circle cx="5.5" cy="5.5" r="4.8" fill="none" stroke="#3a8fd0" stroke-width="1.2"/><path d="M3 5.5H8M6 3.5L8 5.5 6 7.5" fill="none" stroke="#3a8fd0" stroke-width="1.2"/></svg>
      REGISTER FOR THE WEBINAR
    </a>
    <div class="follow">Follow us <span class="social"></span><span class="social"></span><span class="social"></span></div>
  </footer>
</main>
</body>
</html>
```